Automotive component supplier needs a business card design

We need a business card design for our company called Velran Global Components Ltd based in the UK. We are a supplier of interior and exterior components to premium car manufacturers such as Corvel Ashby, Hadley Fenn, Marquist and Tavarelli. We would like to see a modern business card design that uses the colour blue.

Target Market(s)

Premium automotive car manufacturers.

Industry/Entity Type

Automotive

Contact Information for Business Card

Company Name : Velran Global Components Limited
Address: 17 Marlow Yard, Upper Heath, Warwick, CV31 8QL, United Kingdom
Web Address : www.velrancomponents-example.co.uk

Font styles to use
Other font styles liked:
• Helvetica

Colors
3176b5
0255a3
85acd3
cfdeed
cee9f5
85cae6
34a6d7
0692cd
9bcb3c

Requirements
Must have
• Clear company logo and a mixture of blue colours.
Nice to have
• A high quality modern image.
Should not have
• Multiple colours.

```html
<!DOCTYPE html>
<html lang="en">
<head>
<meta charset="utf-8">
<title>Velran Global Components – Business Card</title>
<link rel="stylesheet" href="https://fonts.googleapis.com/css2?family=Open+Sans:wght@400;600;700&display=swap">
<style>
  :root {
    --page-bg: #e9edf1;
    --card-bg: #f7f8f9;
    --brand-blue: #0692cd;
    --band-blue-light: #34a6d7;
    --band-blue-dark: #0a7fbf;
    --accent-green: #9bcb3c;
    --text-grey: #3d3d3d;
    --on-blue: #ffffff;
  }
  * { margin: 0; padding: 0; box-sizing: border-box; }
  html, body {
    width: 1200px;
    height: 900px;
    overflow: hidden;
    background: var(--page-bg);
    font-family: "Open Sans", Helvetica, Arial, sans-serif;
  }
  .business-card {
    position: absolute;
    left: 120px;
    top: 153px;
    width: 960px;
    height: 594px;
    border-radius: 24px;
    overflow: hidden;
    background: var(--card-bg);
    box-shadow: 0 10px 30px rgba(20, 40, 60, 0.18);
  }
  .card-shapes {
    position: absolute;
    inset: 0;
    width: 100%;
    height: 100%;
  }
  .brand {
    position: absolute;
    left: 56px;
    top: 100px;
    color: var(--brand-blue);
    font-weight: 700;
  }
  .brand-name {
    display: block;
    font-size: 92px;
    line-height: 1;
    letter-spacing: 2px;
  }
  .brand-line {
    display: block;
    margin-top: 8px;
    font-size: 21px;
    letter-spacing: 1.6px;
  }
  .contact-person {
    position: absolute;
    left: 58px;
    top: 300px;
    width: 450px;
  }
  .person-name {
    color: var(--brand-blue);
    font-size: 36px;
    font-weight: 600;
    line-height: 1.2;
  }
  .person-role {
    margin-left: 4px;
    color: var(--text-grey);
    font-size: 26px;
    line-height: 1.3;
  }
  .contact-list {
    list-style: none;
    margin: 18px 0 0 4px;
    color: var(--text-grey);
    font-size: 25px;
    line-height: 35px;
    white-space: nowrap;
  }
  .contact-list b { color: var(--brand-blue); font-weight: 700; }
  .contact-list .web { color: var(--brand-blue); font-weight: 700; font-size: 22px; }
  .address {
    position: absolute;
    right: 48px;
    top: 316px;
    color: var(--on-blue);
    font-size: 24px;
    line-height: 34px;
    text-align: right;
    font-style: normal;
    white-space: nowrap;
  }
</style>
</head>
<body>
  <div class="business-card">
    <svg class="card-shapes" viewBox="0 0 650 402" preserveAspectRatio="none" aria-hidden="true">
      <defs>
        <linearGradient id="band-gradient" x1="0" y1="0" x2="1" y2="1">
          <stop offset="0" stop-color="var(--band-blue-light)"/>
          <stop offset="1" stop-color="var(--band-blue-dark)"/>
        </linearGradient>
      </defs>
      <path class="accent-square" fill="var(--accent-green)"
            d="M357,0 H483 V76 Q483,90 469,90 H371 Q357,90 357,76 Z"/>
      <path class="blue-band" fill="url(#band-gradient)"
            d="M510,0 H650 V402 H495 C420,402 357,345 357,270 V115 H498 Q510,115 510,103 Z"/>
    </svg>

    <div class="brand">
      <span class="brand-name">VELRAN</span>
      <span class="brand-line">GLOBAL COMPONENTS</span>
    </div>

    <div class="contact-person">
      <p class="person-name">Daniel Hargrove</p>
      <p class="person-role">Managing Director</p>
      <ul class="contact-list">
        <li><b>P:</b> 01632 960 418</li>
        <li><b>M:</b> 01632 960 418</li>
        <li><b>E:</b> info@velran-example.co.uk</li>
        <li class="web">www.velrancomponents-example.co.uk</li>
      </ul>
    </div>

    <address class="address">
      17 Marlow Yard, Upper Heath,<br>
      Warwick, CV31 8QL,<br>
      United Kingdom
    </address>
  </div>
</body>
</html>
```